Clear Plastic Card Design

I am looking to have a business card designed from my logo icon. I am looking to match the style of a different business card I have attached in the files.
Looking for a card that is plastic, with layers of transparency in the shape of my logo icon (also attached in the files) - not a circle like the other card. The winning design will incorporate the red icon logo on the front and back and include the charity's name, "Light for the Weary Souls" in the same or similar font, as well as an email and phone number. For now, use the email: email@lightfortheweary-mail.org and the phone number 555-382-7194.
We like how the sample business card has transparency, partial and full opacity layers and a matching color scheme. Files will need to be in vector so that our business card printing company can work with it.
UPDATE:
We've some excellent designs in, thank you everyone! I got an early review from the owner, and he requested a minor redirect to find his perfect design. He wants the design to stand out by NOT being a rectangle. Try instead a circle, square, or best yet - something that falls in the outline of the logo icon, either fully or partially. Thank you, everyone!
Light for the Weary Souls text should be incorporated as well as a phone and email.

```html
<!DOCTYPE html>
<html lang="en">
<head>
<meta charset="utf-8">
<title>Light for the Weary Souls – Clear Card</title>
<link href="https://fonts.googleapis.com/css2?family=Lexend:wght@400&family=Arimo:wght@400;700&display=swap" rel="stylesheet">
<style>
  :root {
    --page-bg: #e9e6e3;
    --card-clear: rgba(255, 255, 255, 0.55);
    --card-edge: rgba(255, 255, 255, 0.95);
    --tint-layer: rgba(214, 60, 60, 0.14);
    --brand-red: #d42a22;
    --name-red: #b8191c;
    --ink: #161616;
    --ink-soft: #2a2a2a;
  }
  html, body {
    margin: 0;
    width: 1200px;
    height: 1168px;
    overflow: hidden;
    background: var(--page-bg);
  }
  .canvas {
    position: relative;
    width: 1200px;
    height: 1168px;
  }
  .card {
    position: absolute;
    left: 396px;
    top: 292px;
    width: 543px;
    height: 534px;
    border-radius: 48px;
    background: var(--card-clear);
    border: 3px solid var(--card-edge);
    box-shadow: 0 10px 30px rgba(0, 0, 0, 0.12);
    box-sizing: border-box;
  }
  .tint-layer {
    position: absolute;
    left: 36px;
    top: 34px;
    width: 470px;
    height: 430px;
    border-radius: 36px;
    background: var(--tint-layer);
  }
  .brand-mark {
    position: absolute;
    left: 30px;
    top: 135px;
    width: 150px;
    height: 150px;
    background: var(--brand-red);
    border-radius: 6px;
  }
  .charity-name {
    position: absolute;
    left: 192px;
    top: 122px;
    margin: 0;
    font-family: "Lexend", sans-serif;
    font-weight: 400;
    font-size: 47px;
    line-height: 1.02;
    color: var(--ink);
    letter-spacing: -0.5px;
  }
  .person-name {
    position: absolute;
    left: 192px;
    top: 234px;
    margin: 0;
    font-family: "Arimo", sans-serif;
    font-weight: 700;
    font-size: 31px;
    color: var(--name-red);
  }
  .person-role {
    position: absolute;
    left: 192px;
    top: 276px;
    margin: 0;
    font-family: "Arimo", sans-serif;
    font-size: 18px;
    color: var(--ink-soft);
  }
  .contact-list {
    position: absolute;
    left: 192px;
    top: 310px;
    margin: 0;
    padding: 0;
    list-style: none;
    font-family: "Arimo", sans-serif;
    font-size: 16px;
    color: var(--ink-soft);
  }
  .contact-list li {
    display: flex;
    align-items: center;
    height: 26.5px;
  }
  .contact-icon {
    width: 14px;
    height: 14px;
    margin-right: 9px;
    fill: var(--brand-red);
    flex: none;
  }
</style>
</head>
<body>
<main class="canvas">
  <section class="card" aria-label="Clear plastic business card">
    <div class="tint-layer"></div>
    <div class="brand-mark"></div>
    <h1 class="charity-name">Light for the<br>Weary Souls</h1>
    <p class="person-name">DANIEL REYES</p>
    <p class="person-role">Founder &amp; CEO</p>
    <ul class="contact-list">
      <li>
        <svg class="contact-icon" viewBox="0 0 24 24" aria-hidden="true"><path d="M6.6 10.8a15.1 15.1 0 0 0 6.6 6.6l2.2-2.2a1 1 0 0 1 1-.25 11.4 11.4 0 0 0 3.6.57 1 1 0 0 1 1 1V20a1 1 0 0 1-1 1A17 17 0 0 1 3 4a1 1 0 0 1 1-1h3.5a1 1 0 0 1 1 1c0 1.25.2 2.45.57 3.6a1 1 0 0 1-.25 1z"/></svg>
        555-382-7194
      </li>
      <li>
        <svg class="contact-icon" viewBox="0 0 24 24" aria-hidden="true"><path d="M2 5h20v14H2z M4 7v.5l8 5 8-5V7l-8 5z"/></svg>
        email@lightfortheweary-mail.org
      </li>
      <li>
        <svg class="contact-icon" viewBox="0 0 24 24" aria-hidden="true"><circle cx="12" cy="12" r="10"/></svg>
        lightfortheweary-souls.org
      </li>
    </ul>
  </section>
</main>
</body>
</html>
```